Real Estate Website

Please refer to the attached document. It will be for a real estate agency specialising in commercial and residential sales. looking for Modern and minimalist, Sleek, professional, premium feel

```html
<!DOCTYPE html>
<html lang="en">
<head>
<meta charset="utf-8">
<title>Corvale Group — Commercial &amp; Residential Property</title>
<link href="https://fonts.googleapis.com/css2?family=Poppins:wght@300;400;500;600;700&display=swap" rel="stylesheet">
<style>
:root{
  --orange:#f0532a;
  --orange-soft:#fa7a4e;
  --navy:#24384a;
  --navy-dark:#1e2f3e;
  --ink:#2a2f36;
  --muted:#5d646c;
  --line:#e3e5e8;
  --grey-bg:#f4f4f4;
  --white:#ffffff;
}
*{box-sizing:border-box;margin:0;padding:0}
html,body{width:1200px;height:5063px;overflow:hidden}
body{font-family:"Poppins",sans-serif;color:var(--ink);background:var(--white);position:relative}
section,header,footer{position:absolute;left:0;width:1200px}
.abs{position:absolute}
.brand{display:flex;align-items:center;gap:10px;font-weight:600;font-size:27px;color:var(--navy);letter-spacing:-.3px}
.brand-dot{width:26px;height:26px;border-radius:50%;background:var(--orange)}
.label{display:flex;align-items:center;gap:8px;font-size:12px;font-weight:600;letter-spacing:.3px;color:var(--ink);text-transform:uppercase}
.label::before{content:"";width:13px;height:13px;border-radius:50%;background:var(--orange)}
.label.center{justify-content:center}
.h2{font-size:25px;font-weight:600;color:var(--ink)}
.h2 em{font-style:normal;color:var(--orange)}
.p{font-size:12.5px;line-height:22px;color:var(--muted)}
.btn{display:inline-flex;align-items:center;gap:8px;font-size:12.5px;font-weight:500;border-radius:4px;padding:0 22px;height:42px}
.btn-navy{background:var(--navy);color:#fff}
.btn-orange{background:var(--orange);color:#fff}
.btn svg{width:12px;height:12px}
.ph{background:linear-gradient(135deg,#b9c3cc,#6e7a86)}

/* header */
.site-header{top:0;height:100px;background:#fff}
.site-header .brand{left:95px;top:30px}
.nav{left:338px;top:42px;display:flex;gap:28px;font-size:12.5px;font-weight:500;text-transform:uppercase;color:var(--ink)}
.site-header .btn{left:982px;top:30px;border-radius:22px;height:42px;font-size:12.5px;text-transform:uppercase}

/* hero */
.hero{top:100px;height:640px}
.hero-photo{position:absolute;inset:0;background:linear-gradient(180deg,#b8c6d2 0%,#d8dfe5 45%,#8fa0ae 62%,#6d8f4a 78%,#557a32 100%)}
.hero-title{position:absolute;top:80px;width:100%;text-align:center;color:#fff;font-size:36px;font-weight:700;line-height:52px;text-shadow:0 2px 10px rgba(0,0,0,.25)}
.hero-sub{position:absolute;top:195px;width:100%;text-align:center;color:#fff;font-size:14px}
.hero .btn{position:absolute;left:502px;top:242px;border-radius:22px;height:42px;text-transform:uppercase;font-size:12px}
.hero svg.cut{position:absolute;left:0;bottom:0}

/* about */
.about{top:740px;height:720px}
.about-main{left:0;top:98px;width:508px;height:458px;background:linear-gradient(135deg,#2c3440,#8b8f95 60%,#e9e6e1)}
.about-frame{left:178px;top:82px;width:342px;height:308px;border:1.5px solid #f2b3a2}
.about-small{left:308px;top:398px;width:248px;height:208px;border:8px solid #fff;box-shadow:0 6px 18px rgba(0,0,0,.12);background:linear-gradient(135deg,#dfe6ea,#6f7f8b)}
.about-pin{left:287px;top:370px;width:42px;height:42px;border-radius:50%;background:#fff;box-shadow:0 3px 10px rgba(0,0,0,.15);display:flex;align-items:center;justify-content:center}
.about-pin span{width:18px;height:18px;border-radius:50%;background:var(--orange)}
.about-text{left:601px;top:112px;width:462px}
.about-text .h2{margin:10px 0 18px}
.about-text .p{margin-bottom:10px;font-size:12px;line-height:22px}
.about-text .btn{margin-top:12px}

/* services */
.services{top:1460px;height:610px;background:var(--grey-bg)}
.services .label{position:absolute;top:82px;width:100%}
.services .h2{position:absolute;top:106px;width:100%;text-align:center}
.card{position:absolute;top:165px;width:283px;height:356px;background:#fff;border:1px solid var(--line);border-radius:4px;overflow:hidden}
.card .ph{height:162px}
.card h3{font-size:14px;font-weight:600;margin:18px 16px 8px}
.card .p{margin:0 16px;font-size:12px;line-height:22px}
.card a{position:absolute;left:16px;bottom:22px;font-size:12px;font-weight:500;color:var(--ink);text-decoration:underline;display:flex;align-items:center;gap:8px}

/* why */
.why{top:2070px;height:670px}
.why .label{position:absolute;top:108px;width:100%}
.why .h2{position:absolute;top:132px;width:100%;text-align:center}
.why-ring{left:470px;top:200px;width:260px;height:260px;border-radius:50%;background:#fff;box-shadow:0 8px 30px rgba(0,0,0,.08)}
.why-ring .dash{position:absolute;inset:20px;border:2px dashed var(--navy);border-radius:50%}
.why-ring .brand{position:absolute;left:0;right:0;top:110px;justify-content:center;font-size:26px}
.why-item{position:absolute;width:250px}
.why-item h4{font-size:14px;font-weight:600;margin-bottom:6px}
.why-item .p{font-size:12px;line-height:20px}
.why-item.left{text-align:right}
.icon{position:absolute;width:58px;height:58px;border-radius:50%;display:flex;align-items:center;justify-content:center;border:4px solid #fff;box-shadow:0 0 0 1px var(--line)}
.icon.o{background:var(--orange)}.icon.n{background:var(--navy)}
.icon svg{width:24px;height:24px}
.why .btn{position:absolute;left:498px;top:512px;height:44px}

/* who */
.who{top:2740px;height:525px;background:var(--grey-bg)}
.who-text{left:143px;top:90px;width:450px}
.who-text .h2{margin:10px 0 16px}
.who-text .p{font-size:12px;line-height:22px;margin-bottom:10px}
.who-text .btn{margin-top:14px}
.who-photo{left:642px;top:84px;width:415px;height:346px;border-radius:8px;background:linear-gradient(135deg,#dfe4e8,#a7b0b8 55%,#4f5c66)}

/* testimonials */
.testimonials{top:3265px;height:600px}
.testimonials .label{position:absolute;top:90px;width:100%}
.testimonials .h2{position:absolute;top:114px;width:100%;text-align:center}
.t-card{position:absolute;top:198px;width:283px;height:284px;background:#fff;border-radius:4px;box-shadow:0 4px 20px rgba(0,0,0,.07);padding:54px 22px 0}
.t-quote{position:absolute;left:22px;top:-10px;width:40px;height:40px;border-radius:50%;background:var(--navy);color:#fff;font-size:34px;font-weight:700;line-height:52px;text-align:center}
.t-card:nth-of-type(2) .t-quote{background:var(--orange)}
.stars{color:var(--orange);font-size:17px;letter-spacing:2px}
.g-dot{position:absolute;right:20px;top:50px;width:20px;height:20px;border-radius:50%;border:3px solid var(--line)}
.t-card .p{font-size:12px;line-height:21.5px;color:var(--muted);margin-top:14px}
.t-rule{width:38px;height:2px;background:var(--orange);margin:18px 0 12px}
.t-name{font-size:13px;font-weight:500}
.t-role{font-size:11.5px;color:var(--muted);margin-top:3px}
.arrow{position:absolute;top:326px;width:22px;height:22px;border-radius:50%;display:flex;align-items:center;justify-content:center}
.dots{position:absolute;top:508px;width:100%;display:flex;justify-content:center;gap:8px}
.dots i{width:7px;height:7px;border-radius:50%;background:#d5d8dc}
.dots i.on{background:var(--orange)}

/* contact */
.contact{top:3865px;height:830px}
.contact svg.band{position:absolute;left:0;top:0}
.form-card{left:140px;top:124px;width:918px;height:530px;background:#fff;border-radius:6px;box-shadow:0 10px 40px rgba(0,0,0,.1)}
.form-card .label{position:absolute;top:78px;width:100%}
.form-card .h2{position:absolute;top:102px;width:100%;text-align:center}
.field{position:absolute;height:48px;border:1px solid #d9dcdf;border-radius:3px;display:flex;align-items:center;font-size:12px;color:#7b828a}
.field .ic{width:46px;height:24px;border-right:1px solid #d9dcdf;margin-right:14px;display:flex;align-items:center;justify-content:center}
.field .ic svg{width:14px;height:14px}
.field.msg{align-items:flex-start;padding-top:14px}
.submit{position:absolute;left:122px;top:426px;width:676px;height:46px;background:var(--navy);color:#fff;border-radius:4px;display:flex;align-items:center;justify-content:center;gap:8px;font-size:12.5px;font-weight:500}

/* footer */
.site-footer{top:4695px;height:368px;background:var(--navy-dark);color:#dfe4e8}
.site-footer .brand{position:absolute;left:143px;top:60px;color:#fff}
.f-about{left:143px;top:116px;width:210px;font-size:12px;line-height:20px;color:#c9d0d6}
.follow{left:143px;top:197px;display:flex;align-items:center;gap:8px;font-size:12px}
.follow i{width:20px;height:20px;border-radius:50%;border:1px solid #8593a0}
.follow i.on{background:var(--orange);border-color:var(--orange)}
.f-col h5{font-size:14px;font-weight:500;color:#fff}
.f-col h5::after{content:"";display:block;width:36px;height:2px;background:var(--orange);margin:9px 0 14px}
.f-col li{list-style:none;font-size:12px;line-height:28px;color:#c9d0d6}
.f-col li::before{content:"› ";color:var(--orange)}
.c-row{display:flex;align-items:flex-start;gap:14px;font-size:12px;line-height:20px;color:#c9d0d6;margin-bottom:22px}
.c-row i{flex:none;width:30px;height:30px;border-radius:50%;background:#32475a;display:flex;align-items:center;justify-content:center}
.c-row i.o{background:var(--orange)}
.c-row i svg{width:14px;height:14px}
.copy{left:0;width:100%;top:340px;text-align:center;font-size:11px;color:#aab3bb}
.copy-line{left:0;top:322px;width:100%;height:1px;background:#34495c}
</style>
</head>
<body>

<header class="site-header">
  <div class="abs brand"><span class="brand-dot"></span>Corvale Group</div>
  <nav class="abs nav"><span>Home</span><span>Commercial/Industrial</span><span>Residential</span><span>Business Sales</span><span>About Us</span><span>Info ⌄</span></nav>
  <a class="abs btn btn-orange">Contact Us</a>
</header>

<section class="hero">
  <div class="hero-photo" role="img" aria-label="Modern glass office towers around a green lawn under a cloudy sky"></div>
  <h1 class="hero-title">Specialists in Commercial/ Industrial Property,<br>Trusted in Residential Property</h1>
  <p class="hero-sub">Maximising returns, protecting investments, expert property advisory</p>
  <a class="btn btn-orange">Book an Appraisal</a>
  <svg class="cut" width="1200" height="160" viewBox="0 0 1200 160">
    <polygon points="0,50 1000,157 1200,30 1200,160 0,160" fill="#fff"/>
    <polygon points="0,50 1000,125 1200,30 1000,157" fill="var(--orange)"/>
  </svg>
</section>

<section class="about">
  <div class="abs about-frame"></div>
  <div class="abs about-main" role="img" aria-label="Business people reviewing a floor plan on a desk"></div>
  <div class="abs about-small" role="img" aria-label="Agents shaking hands with a client in an office"></div>
  <div class="abs about-pin"><span></span></div>
  <div class="abs about-text">
    <div class="label">Book an Appraisal</div>
    <h2 class="h2">Discover The Real Value Of <em>Your Property</em></h2>
    <p class="p">At Corvale Group, we don't just provide standard appraisals — we deliver strategic, insight-driven reports that uncover the true drivers of your property's worth. Whether it's commercial, industrial, or residential, our expertise ensures you see the full picture.</p>
    <p class="p">From market trends and rental potential to investment performance and future growth opportunities, our tailored reports give you clarity, confidence, and actionable insights.</p>
    <p class="p">Book a confidential consultation today and gain the expert guidance you need to maximise returns and make smarter property decisions.</p>
    <a class="btn btn-navy">Schedule Consultation <svg viewBox="0 0 12 12"><path d="M2 10L10 2M4 2h6v6" stroke="#fff" stroke-width="1.4" fill="none"/></svg></a>
  </div>
</section>

<section class="services">
  <div class="label center">What We Do</div>
  <h2 class="h2">Property Management, <em>Sales &amp; Leasing</em></h2>
  <article class="card" style="left:140px">
    <div class="ph" role="img" aria-label="Glass commercial building with a paved forecourt" style="background:linear-gradient(160deg,#7f98b3,#c9d3db 60%,#9aa3aa)"></div>
    <h3>Commercial &amp; Industrial</h3>
    <p class="p">Specialist management and leasing of premium commercial and industrial assets, trusted by investors and developers.</p>
    <a>Learn More <svg width="18" height="10" viewBox="0 0 18 10"><path d="M0 5h16M12 1l4 4-4 4" stroke="var(--orange)" stroke-width="1.4" fill="none"/></svg></a>
  </article>
  <article class="card" style="left:459px">
    <div class="ph" role="img" aria-label="Brick family home with a front garden" style="background:linear-gradient(180deg,#a9c4de,#8a5a48 55%,#5d7b3b)"></div>
    <h3>Residential Property</h3>
    <p class="p">Expert residential property management and sales services with proven results and exceptional client outcomes.</p>
    <a>Learn More <svg width="18" height="10" viewBox="0 0 18 10"><path d="M0 5h16M12 1l4 4-4 4" stroke="var(--orange)" stroke-width="1.4" fill="none"/></svg></a>
  </article>
  <article class="card" style="left:776px">
    <div class="ph" role="img" aria-label="Advisors meeting with clients around a laptop" style="background:linear-gradient(135deg,#e3e1dc,#8a8f95 60%,#3b4450)"></div>
    <h3>Property Advisory</h3>
    <p class="p">Comprehensive financial reporting, budgeting, and expense management to optimize cash flow and returns.</p>
    <a>Learn More <svg width="18" height="10" viewBox="0 0 18 10"><path d="M0 5h16M12 1l4 4-4 4" stroke="var(--orange)" stroke-width="1.4" fill="none"/></svg></a>
  </article>
</section>

<section class="why">
  <div class="label center">Why Choose Us</div>
  <h2 class="h2">Commercial &amp; Industrial Property <em>Management &amp; Leasing</em></h2>
  <div class="abs why-ring"><div class="dash"></div><div class="brand"><span class="brand-dot"></span>Corvale</div></div>

  <div class="why-item left" style="left:132px;top:220px"><h4>Sector Expertise</h4><p class="p">Deep knowledge across medical, healthcare, franchise, retail, and industrial sectors, enabling tailored strategies for each asset class.</p></div>
  <div class="icon o" style="left:399px;top:226px"><svg viewBox="0 0 24 24"><circle cx="12" cy="12" r="9" stroke="#fff" stroke-width="1.6" fill="none"/><path d="M12 7l1.5 3.2 3.5.4-2.6 2.3.8 3.4L12 14.6 8.8 16.3l.8-3.4L7 10.6l3.5-.4z" fill="#fff"/></svg></div>

  <div class="why-item left" style="left:132px;top:384px"><h4>Proactive Asset Management</h4><p class="p">Beyond operations, we actively enhance value, mitigate risk, and secure the right tenants.</p></div>
  <div class="icon n" style="left:399px;top:390px"><svg viewBox="0 0 24 24"><path d="M4 14l6-6 4 4 6-6M4 20l6-6 4 4" stroke="#fff" stroke-width="1.6" fill="none"/></svg></div>

  <div class="icon n" style="left:744px;top:226px"><svg viewBox="0 0 24 24"><circle cx="12" cy="12" r="3.5" stroke="#fff" stroke-width="1.6" fill="none"/><circle cx="12" cy="12" r="8" stroke="#fff" stroke-width="1.6" stroke-dasharray="3 2" fill="none"/></svg></div>
  <div class="why-item" style="left:820px;top:220px"><h4>Bespoke Solutions</h4><p class="p">Every property is unique. We craft customised management and leasing strategies aligned with your objectives and market conditions.</p></div>

  <div class="icon o" style="left:744px;top:390px"><svg viewBox="0 0 24 24"><path d="M4 11h4v9H4zM8 11l4-7c2 0 2.5 1.5 2 3.5L13.5 10H19c1 0 1.8.9 1.6 1.9l-1.3 6.5c-.2.9-1 1.6-2 1.6H8" stroke="#fff" stroke-width="1.6" fill="none"/></svg></div>
  <div class="why-item" style="left:820px;top:384px"><h4>Professional Excellence</h4><p class="p">Integrity, precision, and industry-leading best practice.</p></div>

  <a class="btn btn-orange">Book an Appraisal <svg viewBox="0 0 12 12"><path d="M2 10L10 2M4 2h6v6" stroke="#fff" stroke-width="1.4" fill="none"/></svg></a>
</section>

<section class="who">
  <div class="abs who-text">
    <div class="label">Who We Are</div>
    <h2 class="h2">We Are Recognised As <em>A Trusted</em></h2>
    <p class="p">At Corvale Group, we are recognised as a trusted authority in commercial and residential property management, sales, and leasing. Property owners, investors, and developers turn to us for our proven expertise, discretion, and consistent results.</p>
    <p class="p">Our mission is to set the standard for excellence in property services. Guided by innovation, integrity, and strategic execution, we deliver outcomes that protect assets, maximise returns, and create enduring value for our clients.</p>
    <a class="btn btn-navy">Schedule Consultation <svg viewBox="0 0 12 12"><path d="M2 10L10 2M4 2h6v6" stroke="#fff" stroke-width="1.4" fill="none"/></svg></a>
  </div>
  <div class="abs who-photo" role="img" aria-label="Presenter leading a meeting in a bright glass-walled office"></div>
</section>

<section class="testimonials">
  <div class="label center">Testimonials</div>
  <h2 class="h2">What Our Clients Say <em>About Us</em></h2>
  <div class="arrow" style="left:90px;border:1px solid #c4c8cc"><svg width="8" height="10" viewBox="0 0 8 10"><path d="M6 1L2 5l4 4" stroke="#8a9199" stroke-width="1.5" fill="none"/></svg></div>
  <div class="arrow" style="left:1088px;background:var(--navy)"><svg width="8" height="10" viewBox="0 0 8 10"><path d="M2 1l4 4-4 4" stroke="#fff" stroke-width="1.5" fill="none"/></svg></div>
  <div class="t-card" style="left:140px"><div class="t-quote">“</div><div class="stars">★★★★★</div><span class="g-dot"></span><p class="p">"Sed ut perspiciatis unde omnis iste natus error sit voluptatem accusantium laudantium, totam rem aperiam, eaque ipsa quae ab illo inventore veritatis architect"</p><div class="t-rule"></div><div class="t-name">Owen Hartley</div><div class="t-role">Asset Portfolio Manager</div></div>
  <div class="t-card" style="left:459px"><div class="t-quote">“</div><div class="stars">★★★★★</div><span class="g-dot"></span><p class="p">"Sed ut perspiciatis unde omnis iste natus error sit voluptatem accusantium laudantium, totam rem aperiam, eaque ipsa quae ab illo inventore veritatis architect"</p><div class="t-rule"></div><div class="t-name">Lena Moreau</div><div class="t-role">Senior Leasing Specialist</div></div>
  <div class="t-card" style="left:776px"><div class="t-quote">“</div><div class="stars">★★★★★</div><span class="g-dot"></span><p class="p">"Sed ut perspiciatis unde omnis iste natus error sit voluptatem accusantium laudantium, totam rem aperiam, eaque ipsa quae ab illo inventore veritatis architect"</p><div class="t-rule"></div><div class="t-name">Daniel Okafor</div><div class="t-role">Regional Property Director</div></div>
  <div class="dots"><i></i><i class="on"></i><i></i><i></i></div>
</section>

<section class="contact">
  <svg class="band" width="1200" height="830" viewBox="0 0 1200 830">
    <defs><linearGradient id="bandGrad" x1="0" y1="0" x2="0" y2="1"><stop offset="0" stop-color="#f26a3c"/><stop offset="1" stop-color="#fb8c5f"/></linearGradient></defs>
    <polygon points="0,30 1200,0 1200,220 0,220" fill="#f4572d"/>
    <polygon points="0,110 1200,0 1200,820 0,820" fill="url(#bandGrad)"/>
    <polygon points="0,740 1200,720 1200,830 0,830" fill="#f0532a"/>
  </svg>
  <div class="abs form-card">
    <div class="label center">Contact Us</div>
    <h2 class="h2">Ready To Discuss Your <em>Property Goals?</em></h2>
    <div class="field" style="left:122px;top:160px;width:330px"><span class="ic"><svg viewBox="0 0 14 14"><circle cx="7" cy="4.5" r="2.6" stroke="#9aa1a8" fill="none"/><path d="M2 13c0-3 2.2-4.5 5-4.5s5 1.5 5 4.5" stroke="#9aa1a8" fill="none"/></svg></span>First Name</div>
    <div class="field" style="left:468px;top:160px;width:330px"><span class="ic"><svg viewBox="0 0 14 14"><circle cx="7" cy="4.5" r="2.6" stroke="#9aa1a8" fill="none"/><path d="M2 13c0-3 2.2-4.5 5-4.5s5 1.5 5 4.5" stroke="#9aa1a8" fill="none"/></svg></span>Last Name</div>
    <div class="field" style="left:122px;top:224px;width:330px"><span class="ic"><svg viewBox="0 0 14 14"><rect x="1" y="3" width="12" height="8" stroke="#9aa1a8" fill="none"/><path d="M1 3l6 5 6-5" stroke="#9aa1a8" fill="none"/></svg></span>Your Email</div>
    <div class="field" style="left:468px;top:224px;width:330px"><span class="ic"><svg viewBox="0 0 14 14"><path d="M3 1.5l2.5 2.5-1.5 2c.8 1.6 2 2.8 3.6 3.6l2-1.5 2.5 2.5-1.8 1.8C6 12 2 8 1.2 3.3z" stroke="#9aa1a8" fill="none"/></svg></span>Phone</div>
    <div class="field msg" style="left:122px;top:288px;width:676px;height:104px"><span class="ic"><svg viewBox="0 0 14 14"><path d="M2 2h10v7H6l-3 3V9H2z" stroke="#9aa1a8" fill="none"/></svg></span>Your Message</div>
    <div class="submit">Submit Now <svg width="11" height="11" viewBox="0 0 12 12"><path d="M2 10L10 2M4 2h6v6" stroke="#fff" stroke-width="1.4" fill="none"/></svg></div>
  </div>
</section>

<footer class="site-footer">
  <div class="brand"><span class="brand-dot"></span>Corvale Group</div>
  <p class="abs f-about">Sed ut perspiciatis unde omnis iste natus error sit voluptatem accusantium dolorem.</p>
  <div class="abs follow">Follow Us: <i></i><i class="on"></i><i></i></div>
  <div class="abs f-col" style="left:416px;top:62px"><h5>Quick Links</h5><ul><li>Home</li><li>Commercial / Industrial</li><li>Residential</li><li>Business Sales ⌄</li><li>About Us</li><li>Contact us</li></ul></div>
  <div class="abs f-col" style="left:650px;top:62px"><h5>Key Offerings</h5><ul><li>Business listings</li><li>Appraisal report</li><li>What we do</li><li>Who we are</li></ul></div>
  <div class="abs f-col" style="left:838px;top:62px;width:240px"><h5>Contact Us</h5>
    <div class="c-row"><i><svg viewBox="0 0 14 14"><path d="M7 13s4-4.2 4-7.2A4 4 0 003 5.8C3 8.8 7 13 7 13z" stroke="#fff" fill="none"/><circle cx="7" cy="5.8" r="1.4" fill="#fff"/></svg></i><span>123, Lorem ipsum, dolor sit amet, adipiscing elit, 45</span></div>
    <div class="c-row"><i class="o"><svg viewBox="0 0 14 14"><path d="M3 1.5l2.5 2.5-1.5 2c.8 1.6 2 2.8 3.6 3.6l2-1.5 2.5 2.5-1.8 1.8C6 12 2 8 1.2 3.3z" fill="#fff"/></svg></i><span style="line-height:30px">Phone: (123) 555 0147</span></div>
    <div class="c-row"><i><svg viewBox="0 0 14 14"><rect x="1" y="3" width="12" height="8" stroke="#fff" fill="none"/><path d="M1 3l6 5 6-5" stroke="#fff" fill="none"/></svg></i><span style="line-height:30px">hello@corvalegroup.com.au</span></div>
  </div>
  <div class="abs copy-line"></div>
  <p class="abs copy">© 2023 Corvale Business Sales. All Rights Reserved.</p>
</footer>

</body>
</html>
```